Quality Monitoring Company Needs a New Site

We are an established company that has a fair number of clients but the site lacks current design standards that we'd like to keep up with. We'd like to mimic the same style of the site on plinkora.com, vetrumo.com, https://brindlecoffer.com/, etc. We'd also like to make sure the designer understands SEO Silos and how it effects the design elements. Attached is the structure that I'd like to follow for the pages. You don't need to design every single sub-page because they'll probably be fairly similar; however, I want to see at least 1 each. Please use the content on our current site for filler areas. Please try to do a good job of understanding what we do so you can use your best judgement on what is needed to be successful. Use our color scheme and the logo should be the side view but I included the AI just in case.
Updates

I am narrowing down on the field of designs that I have received. There are a lot of similarities between the designs I like and don't like. I'd also like to ensure that some of the inner pages get done in the next 5 days so I can see the creativity that is there as well. That is probably what is next -- getting a few inner pages completed so I can see what you can come up with (not based on our current website) because the current "front pages" are all so good and so close.

Industry/Entity Type

Telecommunications

Colors

Designer to choose colors to be used in the design.

Requirements
Must have
• SEO Silo Look and Feel
• Current Colors
Should not have
• No stockphotos whatsoever. NONE.

```html
<!DOCTYPE html>
<html lang="en">
<head>
<meta charset="utf-8">
<title>Tallyvox — Pricing</title>
<link href="https://fonts.googleapis.com/css2?family=Poppins:wght@300;400;500;600;700&display=swap" rel="stylesheet">
<style>
:root{
  --navy:#002c57;
  --sky:#07b5e8;
  --bg:#f5f7fb;
  --ink:#2d3540;
  --muted:#5c6470;
  --white:#ffffff;
  --frame:#dfe3ec;
  --placeholder-top:#e6eaf1;
  --placeholder-bottom:#d8dee8;
}
*{margin:0;padding:0;box-sizing:border-box}
html,body{width:1108px;height:1200px;overflow:hidden}
body{position:relative;background:var(--bg);font-family:'Poppins',sans-serif;color:var(--ink)}
.abs{position:absolute}
.brand{left:130px;top:60px;display:flex;align-items:center;gap:7px;font-size:21px;font-weight:500;color:var(--navy)}
.brand-dot{width:22px;height:22px;border-radius:50%;background:var(--sky)}
.nav{top:72px;left:373px;display:flex;gap:21px;font-size:12px;color:var(--ink)}
.nav .active{color:var(--sky);font-weight:600}
.call{left:834px;top:59px;display:flex;align-items:center;gap:8px;font-size:13px;font-weight:600;color:var(--navy);letter-spacing:.3px}
.call-icon{width:36px;height:36px;border-radius:50%;background:var(--sky);display:flex;align-items:center;justify-content:center}
.screen{left:266px;top:158px;width:572px;height:387px;border:3px solid var(--frame);border-bottom:none;border-radius:16px 16px 0 0;background:#fafbfe}
.base{left:199px;top:541px;width:706px;height:22px;border-radius:2px 2px 14px 14px;background:linear-gradient(#eef0f6,#cfd5e3)}
.notch{left:502px;top:541px;width:100px;height:8px;border-radius:0 0 6px 6px;background:#d6dbe6}
.illustration{top:251px;height:293px;border-radius:8px;background:linear-gradient(180deg,var(--placeholder-top),var(--placeholder-bottom))}
.illustration-left{left:202px;width:128px}
.illustration-right{left:766px;width:137px}
.title{left:0;width:1108px;top:193px;text-align:center;font-size:27px;font-weight:700;color:var(--navy)}
.title-rule{left:538px;top:241px;width:33px;height:2px;background:var(--sky)}
.label{top:266px;width:194px;text-align:center;font-size:9.5px;font-weight:600;color:var(--navy)}
.field{top:288px;width:194px;height:29px;border:1px solid #cfe9ef;border-radius:10px;background:var(--white);box-shadow:0 3px 8px rgba(0,40,90,.06);display:flex;align-items:center;justify-content:center;font-size:11.5px;color:var(--muted)}
.note{left:0;width:1108px;top:348px;text-align:center;font-size:8px;color:var(--navy)}
.stat{top:377px;width:110px;text-align:center;color:var(--navy)}
.stat .k{font-size:9.5px;font-weight:600}
.stat .v{font-size:18px;font-weight:700;color:var(--sky);line-height:1.2}
.stat .s{font-size:6px;color:var(--ink)}
.total{left:609px;top:369px;width:103px;height:45px;background:var(--sky);border-radius:2px;color:var(--white);text-align:center;padding-top:5px}
.total .v{font-size:16px;font-weight:700;line-height:1.1}
.total .s{font-size:8.5px;font-weight:600}
.btn{height:32px;border-radius:16px;background:var(--navy);color:var(--white);font-size:12.5px;letter-spacing:.5px;display:flex;align-items:center;justify-content:center}
.intro{left:224px;width:660px;top:602px;text-align:center;font-size:10.3px;line-height:17.5px;color:var(--muted);letter-spacing:.1px}
.footer{left:0;top:855px;width:1108px;height:345px;background:var(--navy)}
.shout{left:195px;top:758px;width:717px;height:195px;border-radius:98px;background:var(--sky)}
.shout h2{position:absolute;left:0;width:717px;top:44px;text-align:center;font-size:38px;font-weight:400;color:var(--white);letter-spacing:1px}
.foot-h{top:1003px;font-size:16px;font-weight:700;color:var(--sky)}
.links{top:1036px;font-size:10.5px;line-height:18.8px;color:var(--white);list-style:none}
.contact-line{font-size:12px;color:var(--white);display:flex;gap:8px;line-height:21px}
.foot-brand{left:842px;top:1038px;display:flex;align-items:center;gap:10px;font-size:24px;font-weight:500;color:var(--white)}
.foot-brand .brand-dot{width:30px;height:30px}
.divider{left:129px;top:1157px;width:848px;height:1px;background:rgba(255,255,255,.15)}
.copy{left:0;width:1108px;top:1170px;text-align:center;font-size:11.5px;color:var(--white)}
</style>
</head>
<body>
<header>
  <div class="abs brand"><span class="brand-dot"></span>Tallyvox</div>
  <nav class="abs nav"><span>Home</span><span>Services</span><span>Industries</span><span class="active">Pricing</span><span>Team</span><span>Blog</span><span>Contact Us</span></nav>
  <div class="abs call"><span class="call-icon"><svg width="15" height="15" viewBox="0 0 24 24"><path fill="#fff" d="M6.6 10.8a15.1 15.1 0 0 0 6.6 6.6l2.2-2.2a1 1 0 0 1 1-.25 11.4 11.4 0 0 0 3.6.57 1 1 0 0 1 1 1V20a1 1 0 0 1-1 1A17 17 0 0 1 3 4a1 1 0 0 1 1-1h3.5a1 1 0 0 1 1 1c0 1.25.2 2.45.57 3.57a1 1 0 0 1-.25 1z"/></svg></span>800-555-0142</div>
</header>

<main>
  <div class="abs screen"></div>
  <div class="abs base"></div>
  <div class="abs notch"></div>
  <div class="abs illustration illustration-left" role="img" aria-label="Illustration of a woman holding a laptop"></div>
  <div class="abs illustration illustration-right" role="img" aria-label="Illustration of a man holding a folder"></div>

  <h1 class="abs title">Pricing</h1>
  <div class="abs title-rule"></div>
  <div class="abs label" style="left:353px"># of Calls / Month*</div>
  <div class="abs label" style="left:561px">Average Call Length*</div>
  <div class="abs field" style="left:353px">5,000</div>
  <div class="abs field" style="left:561px">6</div>
  <p class="abs note">Starting at $.20 per call minute</p>
  <div class="abs stat" style="left:390px"><div class="k">Total Minutes</div><div class="v">30,000</div><div class="s">30,000 minutes minimum</div></div>
  <div class="abs stat" style="left:492px"><div class="k">Cost Per Min</div><div class="v">$0.20</div></div>
  <div class="abs total"><div class="v">$6,000</div><div class="s">+ $999 setup fee</div></div>
  <div class="abs btn" style="left:483px;top:453px;width:143px">GET STARTED</div>

  <p class="abs intro">Contact us today to learn more! We will have someone contact you to discuss pricing, show you a demonstration of our<br>system, and answer all of your questions. We look forward to discussing your quality processes!</p>
  <div class="abs btn" style="left:463px;top:660px;width:182px">CONTACT US NOW</div>
</main>

<footer>
  <div class="abs footer"></div>
  <div class="abs shout">
    <h2>Give Us A Shout</h2>
    <div class="abs btn" style="left:287px;top:117px;width:143px">GET IN TOUCH</div>
  </div>

  <h3 class="abs foot-h" style="left:128px">Quick Links</h3>
  <ul class="abs links" style="left:128px"><li>Home</li><li>Services</li><li>System Details</li><li>Pricing</li></ul>
  <ul class="abs links" style="left:271px"><li>Team</li><li>Blog</li><li>Contact Us</li><li>Login</li></ul>

  <h3 class="abs foot-h" style="left:424px">Contact Us</h3>
  <div class="abs contact-line" style="left:426px;top:1035px">
    <svg width="11" height="15" viewBox="0 0 24 32" style="margin-top:4px"><path fill="#fff" d="M12 0C5.4 0 0 5.4 0 12c0 9 12 20 12 20s12-11 12-20C24 5.4 18.6 0 12 0zm0 17a5 5 0 1 1 0-10 5 5 0 0 1 0 10z"/></svg>
    <span>4410 Marlow Ave.<br>Fairhaven, CA 90000</span>
  </div>
  <div class="abs contact-line" style="left:609px;top:1035px">
    <svg width="13" height="13" viewBox="0 0 24 24" style="margin-top:4px"><path fill="#fff" d="M6.6 10.8a15.1 15.1 0 0 0 6.6 6.6l2.2-2.2a1 1 0 0 1 1-.25 11.4 11.4 0 0 0 3.6.57 1 1 0 0 1 1 1V20a1 1 0 0 1-1 1A17 17 0 0 1 3 4a1 1 0 0 1 1-1h3.5a1 1 0 0 1 1 1c0 1.25.2 2.45.57 3.57a1 1 0 0 1-.25 1z"/></svg>
    <span>800-555-0142</span>
  </div>
  <div class="abs contact-line" style="left:609px;top:1068px">
    <svg width="13" height="10" viewBox="0 0 24 18" style="margin-top:6px"><path fill="#fff" d="M0 0h24v2L12 10 0 2zM0 4.5l12 8 12-8V18H0z"/></svg>
    <span>hello@tallyvox.com</span>
  </div>

  <div class="abs foot-brand"><span class="brand-dot"></span>Tallyvox</div>
  <div class="abs divider"></div>
  <p class="abs copy">Copyright © 2019 TALLYVOX. All Rights Reserved.</p>
</footer>
</body>
</html>
```